Bright Harbor, LLC Business Card Design

We need a product business card designed for a new company Bright Harbor, LLC. We make and resell waterless RV cleaner, polish and protectant. It cleans and protects in a simple spray and wipe step leaving the surface protected and conditioned to repel dust, dirt, water, smudges, bugs and fingerprints while preventing fogging. Safe on acrylic, plexiglas, lexan, plastic, rubber, painted surfaces, chrome, stainless, aluminum, vinyl, leather, glass.... This is an eco-friendly green product.

We want to play off the company name to tell the consumer that the product is easy to use and associate to the nostalgics 1950's in the USA... Thinking old travel trailer with hot rod truck pulling it as the graphic, maybe the husband cleaning the truck and the wife cleaning the trailer for a Bright Harbor surface.
Updates

Just posted our newly finished logo. Need to have "Cleaner and Protectant" added to the design as well. Thanks everyone that has submitted thus far, i am working to get comments on all.

If you need a different file format, please let me know. Thank you.

Most important info, is the logo, website and the words "Cleaner" or "Clean" along "Protectant" or "Protect" the remainder is of less importance. Highlight: www.brightharborwash.example Focus is on company brand for Brighter Harbor Cleaner product: However, need a section for the following contact info: Walt Ferris (xxx) xxx-xxxx email address Would like space for QR Code if possible.

Target Market(s)

Adults in the USA between ages of 35-75 that are actively involved in the Recreational Vehicle (RV), travel trailer, and hot rod lifestyle. We are targeting the RV marked of the high end travel, 5th wheel and bus RV market. Along with hot rods, automotive and motorcycle market.

Industry/Entity Type

Travel

Requirements
Must have
• Most important info, is the logo, website and the words "Cleaner" or "Clean" along "Protectant" or "Protect" the remainder is of less importance.

Highlight:
www.brightharborwash.example

Focus is on company brand for Brighter Harbor Cleaner product: However, need a section for the following contact info:

Walt Ferris
(xxx) xxx-xxxx
email address
Nice to have
• Would like a space for a QR Code.

```html
<!DOCTYPE html>
<html lang="en">
<head>
<meta charset="utf-8">
<title>Bright Harbor, LLC Business Card</title>
<link rel="stylesheet" href="https://fonts.googleapis.com/css2?family=Open+Sans:wdth,wght@75..100,400;75..100,600&display=swap">
<style>
  :root {
    --bg: #e4e5e7;
    --blue-light: #0a80c2;
    --blue-deep: #0b5aa6;
    --paper: #ffffff;
    --orange: #e88a1e;
    --ink-light: #ffffff;
    --art-tone-a: rgba(120, 170, 215, 0.45);
    --art-tone-b: rgba(20, 60, 110, 0.55);
  }
  * { box-sizing: border-box; margin: 0; padding: 0; }
  html, body { width: 1200px; height: 720px; overflow: hidden; }
  body {
    background: var(--bg);
    font-family: "Open Sans", Arial, sans-serif;
    position: relative;
  }
  .card {
    position: absolute;
    top: 217px;
    width: 500px;
    height: 285px;
    background: linear-gradient(160deg, var(--blue-light) 0%, var(--blue-deep) 100%);
    overflow: hidden;
  }
  .card--front { left: 60px; }
  .card--back { left: 640px; }

  .paper-band { position: absolute; background: var(--paper); }
  .card--front .paper-band--side { right: 0; top: 0; width: 35px; height: 100%; }
  .card--front .paper-band--base { right: 0; bottom: 0; width: 213px; height: 29px; }
  .card--back .paper-band--side { left: 0; top: 0; width: 35px; height: 100%; }
  .card--back .paper-band--base { left: 0; bottom: 0; width: 213px; height: 28px; }

  .brand-name {
    position: absolute;
    color: var(--orange);
    font-weight: 400;
    font-stretch: 75%;
    letter-spacing: -0.5px;
    white-space: nowrap;
  }
  .card--front .brand-name { left: 24px; top: 112px; font-size: 32px; line-height: 38px; }
  .card--back .brand-name { left: 224px; bottom: 3px; font-size: 32px; line-height: 36px; }

  .tagline {
    position: absolute;
    left: 26px;
    top: 152px;
    color: var(--ink-light);
    font-size: 13px;
    line-height: 17px;
    letter-spacing: 0.3px;
  }
  .website {
    position: absolute;
    left: 26px;
    top: 171px;
    color: var(--orange);
    font-weight: 600;
    font-size: 12px;
    line-height: 16px;
  }
  .qr-space {
    position: absolute;
    left: 26px;
    top: 202px;
    width: 56px;
    height: 56px;
    border: 1.5px dashed rgba(255, 255, 255, 0.7);
    border-radius: 3px;
  }

  .contact-person { position: absolute; left: 342px; top: 84px; }
  .contact-person__name { color: var(--ink-light); font-weight: 600; font-size: 15px; line-height: 18px; }
  .contact-person__role { color: var(--orange); font-size: 12px; line-height: 14px; }

  .contact-list {
    position: absolute;
    right: 54px;
    top: 128px;
    list-style: none;
  }
  .contact-list li {
    display: flex;
    justify-content: flex-end;
    align-items: center;
    gap: 8px;
    color: var(--ink-light);
    font-size: 12px;
    line-height: 19.5px;
    white-space: nowrap;
  }
  .contact-list svg { width: 11px; height: 11px; fill: var(--orange); flex: none; }

  .vehicle-art {
    position: absolute;
    left: 66px;
    top: 49px;
    width: 400px;
    height: 168px;
    border-radius: 40px 60px 20px 20px;
    background: linear-gradient(180deg, var(--art-tone-a) 0%, var(--art-tone-b) 100%);
  }
</style>
</head>
<body>
  <section class="card card--front" aria-label="Card front">
    <div class="paper-band paper-band--side"></div>
    <div class="paper-band paper-band--base"></div>
    <p class="brand-name">Bright Harbor, LLC</p>
    <p class="tagline">Cleaner and Protectant</p>
    <p class="website">www.brightharborwash.example</p>
    <div class="qr-space" role="img" aria-label="Space reserved for QR code"></div>
    <div class="contact-person">
      <p class="contact-person__name">Walt Ferris</p>
      <p class="contact-person__role">Manager</p>
    </div>
    <ul class="contact-list">
      <li>555-210-4417
        <svg viewBox="0 0 24 24" aria-hidden="true"><path d="M6.6 10.8a15 15 0 0 0 6.6 6.6l2.2-2.2c.3-.3.7-.4 1-.2 1.1.4 2.3.6 3.6.6.6 0 1 .4 1 1V20c0 .6-.4 1-1 1A17 17 0 0 1 3 4c0-.6.4-1 1-1h3.5c.6 0 1 .4 1 1 0 1.3.2 2.5.6 3.6.1.3 0 .7-.2 1z"/></svg>
      </li>
      <li>555-210-4418
        <svg viewBox="0 0 24 24" aria-hidden="true"><path d="M6.6 10.8a15 15 0 0 0 6.6 6.6l2.2-2.2c.3-.3.7-.4 1-.2 1.1.4 2.3.6 3.6.6.6 0 1 .4 1 1V20c0 .6-.4 1-1 1A17 17 0 0 1 3 4c0-.6.4-1 1-1h3.5c.6 0 1 .4 1 1 0 1.3.2 2.5.6 3.6.1.3 0 .7-.2 1z"/></svg>
      </li>
      <li>HarborDesk@mailbay.example
        <svg viewBox="0 0 24 24" aria-hidden="true"><path d="M2 5h20v14H2z"/><path d="M2 5l10 7 10-7" fill="none" stroke="#0b5aa6" stroke-width="1.6"/></svg>
      </li>
      <li>4820 Cedar Lane Fairhaven, CA 90000
        <svg viewBox="0 0 24 24" aria-hidden="true"><path d="M12 2a7 7 0 0 0-7 7c0 5 7 13 7 13s7-8 7-13a7 7 0 0 0-7-7zm0 9.5A2.5 2.5 0 1 1 12 6.5a2.5 2.5 0 0 1 0 5z"/></svg>
      </li>
    </ul>
  </section>

  <section class="card card--back" aria-label="Card back">
    <div class="paper-band paper-band--side"></div>
    <div class="paper-band paper-band--base"></div>
    <div class="vehicle-art" role="img" aria-label="Illustration of a vintage two-door SUV in blue tones"></div>
    <p class="brand-name">Bright Harbor, LLC</p>
  </section>
</body>
</html>
```